Company selling food supplements with CBD needs label.

We need a label design for a company called "VEKA Works ltd", is based in the UK, the market name is "VEKA" or "VEKA Very Easy Kindly Aged". The initial product is Virgin Organic Hemp Seed Oil with a CBD in a 10ml amber dropper bottle. The design should be simplicity and luxury. The design should include also box.

Target Market(s)

Food supplements on Tradeshelf UK

Industry/Entity Type

Supplement

Font styles to use
Other font styles liked:
• Some luxury

Colors

Designer to choose colors to be used in the design.

Requirements
Must have
• All the information on the label required by the UK for the food supplements, the same on the box. One version matt one transparent. The design should include different CBD content, one different bottle (250mg, 500mg, 750mg, 1000mg) .
• The label and box should include the following phrases: "DIRECTIONS: Food Supplement. Shake well before use. Use 4-6 drops 2-3 times a day. Leave the oil in your mouth for 30-60 seconds before swallowing. Gradually build up the dose to find your optimum dosage.
• CAUTION: Do not exceed the recommended daily intake. Do not use as a substitute for a varied diet. Do not use during pregnancy and breastfeeding. Store in a dark and cool place, away from sunlight. Keep away from children.
• INGREDIENTS: Hemp Seed Oil, Omega-6 (2800mg), Omega-3 (930mg), CBD (250mg)
• MANUFACTURED: VEKA Works Ltd, 87 Pelbury Rd, Harrow, HA7 2QX, www,vekaworks.example, info@vekaworks.example.
• EXPIRED DATE: "
• The box should also include a place for bark code.
Nice to have
• Simple and elegant design vertical or horizontal with exposed company logo "VEKA" or "VEKA Very Easy Kindly Aged". The company logo is provided but designers may change it freely.
Should not have
• The best without pictures/graphics overloading simplicity and purity of design.

```html
<!DOCTYPE html>
<html lang="en">
<head>
<meta charset="UTF-8">
<title>VEKA Hemp Oil CBD Drops Label</title>
<link rel="stylesheet" href="https://fonts.googleapis.com/css2?family=Montserrat:wght@400;500&family=Josefin+Sans:wght@400;600;700&display=swap">
<style>
  :root {
    --canvas: #f4f4f4;
    --label-black: #1e1d1d;
    --label-green: #3dbb4a;
    --ink-dark: #2a2a2a;
    --ink-white: #ffffff;
    --ink-green: #45c652;
  }
  * { margin: 0; padding: 0; box-sizing: border-box; }
  html, body {
    width: 1200px;
    height: 900px;
    overflow: hidden;
    background: var(--canvas);
  }
  .canvas {
    width: 1200px;
    height: 900px;
    display: flex;
    align-items: center;
    justify-content: center;
  }
  .label {
    width: 420px;
    height: 620px;
    background: var(--label-green);
    display: flex;
    flex-direction: column;
    overflow: hidden;
  }
  .label__brand {
    background: var(--label-black);
    border-radius: 0 0 34px 34px;
    height: 220px;
    display: flex;
    flex-direction: column;
    align-items: center;
    justify-content: center;
    padding-top: 20px;
  }
  .brand-name {
    font-family: "Montserrat", sans-serif;
    font-weight: 400;
    font-size: 104px;
    line-height: 1;
    letter-spacing: 2px;
    color: var(--ink-white);
  }
  .brand-tagline {
    margin-top: 16px;
    font-family: "Montserrat", sans-serif;
    font-weight: 500;
    font-size: 13px;
    letter-spacing: 0.5px;
    color: var(--ink-white);
    text-transform: uppercase;
  }
  .label__product {
    height: 130px;
    display: flex;
    flex-direction: column;
    align-items: center;
    justify-content: center;
    color: var(--ink-dark);
    font-family: "Josefin Sans", sans-serif;
  }
  .product-kind {
    font-weight: 600;
    font-size: 27px;
    letter-spacing: 2px;
    line-height: 1;
  }
  .product-name {
    margin-top: 8px;
    font-weight: 700;
    font-size: 58px;
    line-height: 1;
    letter-spacing: 1px;
  }
  .label__strength {
    flex: 1;
    background: var(--label-black);
    border-radius: 34px 34px 0 0;
    display: flex;
    flex-direction: column;
    align-items: center;
    padding-top: 26px;
    font-family: "Josefin Sans", sans-serif;
  }
  .strength-amount {
    font-family: "Montserrat", sans-serif;
    font-weight: 400;
    font-size: 56px;
    line-height: 1;
    color: var(--ink-white);
  }
  .strength-product {
    margin-top: 10px;
    font-weight: 700;
    font-size: 52px;
    line-height: 1;
    letter-spacing: 1px;
    color: var(--ink-green);
  }
  .volume-pill {
    margin-top: 38px;
    background: var(--label-green);
    color: var(--ink-dark);
    border-radius: 12px;
    padding: 10px 22px 6px;
    font-weight: 600;
    font-size: 38px;
    line-height: 1;
  }
</style>
</head>
<body>
  <main class="canvas">
    <section class="label" aria-label="VEKA hemp oil CBD drops bottle label">
      <header class="label__brand">
        <h1 class="brand-name">VEKA</h1>
        <p class="brand-tagline">Very Easy Kindly Aged</p>
      </header>
      <div class="label__product">
        <p class="product-kind">VIRGIN ORGANIC</p>
        <h2 class="product-name">HEMP OIL</h2>
      </div>
      <div class="label__strength">
        <p class="strength-amount">1000mg</p>
        <p class="strength-product">CBD DROPS</p>
        <p class="volume-pill">10ml</p>
      </div>
    </section>
  </main>
</body>
</html>
```